Tech business card design

We need an amazing business card design for our new business 'Pexla' a marketing tech startup based in Sydney, Australia. We provide an online marketplace for businesses to search and buy advertising media, connect with service providers and learn more about marketing. We wish to communicate 'cool tech', reliability and professionalism and design based around our logo.

Target Market(s)

Business Owners

Contact Information for Business Card

Name
Position
Email Address
Website
Phone Number

Font styles to use
Other font styles liked:
• Avenir & Avenir Next

Colors

Designer to choose colors to be used in the design.

```html
<!DOCTYPE html>
<html lang="en">
<head>
<meta charset="utf-8">
<title>Pexla Business Card</title>
<link href="https://fonts.googleapis.com/css2?family=Nunito+Sans:wght@400;700;900&display=swap" rel="stylesheet">
<style>
  :root {
    --stage: #e0dddd;
    --paper: #ffffff;
    --navy: #23264a;
    --navy-deep: #14163a;
    --navy-glow: #34396a;
    --ink: #2b2b2b;
    --rule: #2a2d52;
    --edge: #555555;
  }
  * { margin: 0; padding: 0; box-sizing: border-box; }
  html, body { width: 975px; height: 1200px; overflow: hidden; background: var(--stage); }
  body { position: relative; font-family: "Nunito Sans", Arial, sans-serif; color: var(--ink); }

  .card {
    position: absolute; left: 57px; width: 859px; height: 491px;
    background: var(--paper); border: 1px solid var(--edge); overflow: hidden;
  }
  .card--front { top: 70px; }
  .card--back { top: 628px; }
  .card svg.shapes { position: absolute; inset: 0; width: 100%; height: 100%; }

  .holder { position: absolute; left: 82px; top: 72px; }
  .holder__name { font-size: 33px; font-weight: 700; letter-spacing: 0.2px; line-height: 1; color: #1e1e1e; }
  .holder__role { font-size: 28px; font-weight: 400; margin-top: 10px; line-height: 1; }

  .divider { position: absolute; left: 442px; top: 31px; width: 4px; height: 161px; background: var(--rule); }

  .contacts { position: absolute; left: 497px; top: 38px; list-style: none; font-size: 20px; line-height: 1; }
  .contacts li { display: flex; align-items: center; height: 32px; }
  .contacts svg { width: 20px; height: 20px; margin-right: 10px; flex: none; }
  .contacts .address { display: block; height: auto; line-height: 29px; margin-top: 4px; }

  .wordmark {
    position: absolute; font-weight: 900; font-size: 104px; line-height: 1;
    color: var(--navy-deep); letter-spacing: -1px;
  }
  .card--front .wordmark { left: 463px; top: 256px; }
  .card--back .wordmark { left: 46px; top: 266px; }

  .back-url {
    position: absolute; left: 0; right: 0; top: 430px; text-align: center;
    color: var(--paper); font-size: 26px; letter-spacing: 3px;
  }
</style>
</head>
<body>

<section class="card card--front">
  <svg class="shapes" viewBox="0 0 859 491" aria-hidden="true">
    <defs>
      <radialGradient id="stripeGlow" cx="0.5" cy="0.5" r="0.6">
        <stop offset="0" stop-color="var(--navy-glow)"/>
        <stop offset="1" stop-color="var(--navy)"/>
      </radialGradient>
    </defs>
    <rect x="0" y="220" width="859" height="196" fill="none" stroke="#111" stroke-width="2"/>
    <polygon points="0,240 55,240 125,401 0,401" fill="url(#stripeGlow)"/>
    <polygon points="92,240 188,240 287,401 168,401" fill="url(#stripeGlow)"/>
    <rect x="0" y="416" width="859" height="75" fill="var(--navy)"/>
  </svg>

  <div class="holder">
    <p class="holder__name">JOHN SMITH</p>
    <p class="holder__role">Position</p>
  </div>

  <div class="divider"></div>

  <ul class="contacts">
    <li>
      <svg viewBox="0 0 20 20" aria-hidden="true"><circle cx="10" cy="10" r="8.5" fill="none" stroke="var(--navy)" stroke-width="1.8"/><path d="M7 5.5l1.8 2.3-1 1.2a6 6 0 0 0 3.2 3.2l1.2-1 2.3 1.8-1.2 1.6c-3.8-.3-7.6-4.1-7.9-7.9z" fill="var(--navy)"/></svg>
      012-345-6789
    </li>
    <li>
      <svg viewBox="0 0 20 20" aria-hidden="true"><rect x="1.5" y="4" width="17" height="12" fill="var(--navy)"/><path d="M1.5 4l8.5 7 8.5-7M1.5 16l6-5.5M18.5 16l-6-5.5" fill="none" stroke="#fff" stroke-width="1.4"/></svg>
      info@pexla.com
    </li>
    <li>
      <svg viewBox="0 0 20 20" aria-hidden="true"><g fill="none" stroke="var(--navy)" stroke-width="1.5"><circle cx="10" cy="10" r="8.5"/><ellipse cx="10" cy="10" rx="3.8" ry="8.5"/><path d="M1.5 10h17M3 5.5h14M3 14.5h14"/></g></svg>
      www.pexla.com
    </li>
    <li class="address">Street name City Name,<br>Zipcode,012345</li>
  </ul>

  <p class="wordmark">Pexla</p>
</section>

<section class="card card--back">
  <svg class="shapes" viewBox="0 0 859 491" aria-hidden="true">
    <defs>
      <linearGradient id="bandGlow" x1="0" y1="0" x2="1" y2="1">
        <stop offset="0" stop-color="var(--navy)"/>
        <stop offset="0.5" stop-color="var(--navy-glow)"/>
        <stop offset="1" stop-color="var(--navy)"/>
      </linearGradient>
    </defs>
    <polygon points="0,232 425,232 589,394 0,394" fill="var(--paper)" stroke="#aaa" stroke-width="2"/>
    <polygon points="425,232 589,232 748,394 589,394" fill="url(#bandGlow)"/>
    <rect x="716" y="366" width="143" height="30" fill="var(--navy)"/>
    <rect x="0" y="394" width="859" height="97" fill="var(--navy)"/>
  </svg>

  <p class="wordmark">Pexla</p>
  <p class="back-url">www.pexla.com</p>
</section>

</body>
</html>
```